Disability provider requiring digital flyer to promote services

My company works within the Disability sector (KTAP registered provider), currently operating in Sydney, Australia.
I require a digital brochure which lists our services and gives potential customers a quick look into what we do with a single glance.
Undecided whether this digital flyer is to be single or double sided, happy to consult with an experienced designer in this regard.
I prefer minimalist designs (which may be an issue for someone trying to convey information, I'm not sure), and possibly someone who can work with out watercolor logo.
Services include:
-Supported Independent Living
-Specialist Disability Accommodation
-Individualised Living Options Stage 1 & 2
-Home Modifications
-Occupational Therapy
-Support Coordination Levels 1 & 2
-Short Term Accommodation - STA Respite
-Drop In Supports
-Community Access
Disability

```html
<!DOCTYPE html>
<html lang="en">
<head>
<meta charset="utf-8">
<title>Sunward Care – Services Flyer</title>
<link rel="stylesheet" href="https://fonts.googleapis.com/css2?family=Oswald:wght@500&family=Roboto+Condensed:wght@300&family=Raleway:wght@300&display=swap">
<style>
  :root {
    --paper: #ffffff;
    --ink-grey: #5b5d60;
    --rule-grey: #6d6f72;
    --pill-grey: #5f6164;
    --gold: #f2c36b;
    --teal: #19a9cf;
    --photo-blue: #3a5a7e;
    --photo-grey: #b9b9bb;
    --photo-orange: #e9893a;
    --wash-pink: #f2b6d3;
    --wash-teal: #7fd3e0;
    --wash-orange: #f8c99a;
  }
  * { box-sizing: border-box; margin: 0; padding: 0; }
  html, body { width: 1200px; height: 1036px; overflow: hidden; background: var(--paper); }
  .flyer { position: relative; width: 1200px; height: 1036px; background: var(--paper); overflow: hidden; }

  .hero-photo {
    position: absolute; left: 0; top: 0; width: 1200px; height: 580px;
    background:
      radial-gradient(circle at 300px 330px, var(--photo-orange) 0 110px, transparent 112px),
      radial-gradient(ellipse at 820px 200px, var(--photo-grey) 0 260px, transparent 380px),
      radial-gradient(ellipse at 160px 140px, var(--photo-blue) 0 120px, transparent 200px),
      linear-gradient(180deg, #e9eaec 0%, #f3f3f4 70%, var(--paper) 100%);
  }

  .watermark-circle {
    position: absolute; left: 760px; top: 470px; width: 300px; height: 300px;
    border-radius: 50%;
    background: radial-gradient(circle, rgba(242,182,211,.35), rgba(248,201,154,.15) 70%, transparent);
  }

  .brand { position: absolute; left: 230px; top: 600px; display: flex; align-items: center; gap: 16px; }
  .brand-dot { width: 34px; height: 34px; border-radius: 50%; background: var(--teal); }
  .brand-name {
    font-family: "Raleway", sans-serif; font-weight: 300; font-size: 56px;
    letter-spacing: 2px; color: var(--ink-grey); text-transform: uppercase;
  }

  .section-rule { position: absolute; left: 0; top: 730px; width: 1200px; height: 4px; background: var(--rule-grey); }
  .section-tag {
    position: absolute; left: 240px; top: 706px; padding: 8px 28px;
    background: var(--pill-grey); border-radius: 26px;
    font-family: "Oswald", sans-serif; font-weight: 500; font-size: 32px;
    color: var(--gold); text-transform: uppercase; letter-spacing: .5px;
  }

  .service-list { position: absolute; top: 780px; list-style: none; }
  .service-list.col-left { left: 260px; }
  .service-list.col-right { left: 720px; }
  .service-item {
    display: flex; align-items: center; gap: 14px; height: 34px;
    font-family: "Roboto Condensed", sans-serif; font-weight: 300; font-size: 24px; color: var(--ink-grey);
  }
  .service-item svg { flex: none; }

  .grass-wash {
    position: absolute; left: 0; bottom: 0; width: 1200px; height: 80px;
    background: linear-gradient(90deg, var(--wash-teal), #c5e9ef 45%, var(--wash-pink) 70%, var(--wash-orange));
    opacity: .85;
  }
</style>
</head>
<body>
<main class="flyer">
  <div class="hero-photo" role="img" aria-label="Photo of a person in a wheelchair reaching for a bouncing basketball"></div>
  <div class="watermark-circle"></div>

  <div class="brand">
    <span class="brand-dot"></span>
    <span class="brand-name">Sunward Care</span>
  </div>

  <div class="section-rule"></div>
  <h2 class="section-tag">Services We Provided</h2>

  <ul class="service-list col-left">
    <li class="service-item"><svg width="20" height="16" viewBox="0 0 20 16"><ellipse cx="10" cy="8" rx="9" ry="7" fill="var(--teal)"/><circle cx="10" cy="8" r="3" fill="#fff"/></svg>Supported Independent Living</li>
    <li class="service-item"><svg width="20" height="16" viewBox="0 0 20 16"><ellipse cx="10" cy="8" rx="9" ry="7" fill="var(--teal)"/><circle cx="10" cy="8" r="3" fill="#fff"/></svg>Specialist Disability Accommodation</li>
    <li class="service-item"><svg width="20" height="16" viewBox="0 0 20 16"><ellipse cx="10" cy="8" rx="9" ry="7" fill="var(--teal)"/><circle cx="10" cy="8" r="3" fill="#fff"/></svg>Individualised Living Options Stage 1 &amp; 2</li>
    <li class="service-item"><svg width="20" height="16" viewBox="0 0 20 16"><ellipse cx="10" cy="8" rx="9" ry="7" fill="var(--teal)"/><circle cx="10" cy="8" r="3" fill="#fff"/></svg>Home Modifications</li>
  </ul>

  <ul class="service-list col-right">
    <li class="service-item"><svg width="20" height="16" viewBox="0 0 20 16"><ellipse cx="10" cy="8" rx="9" ry="7" fill="var(--teal)"/><circle cx="10" cy="8" r="3" fill="#fff"/></svg>Occupational Therapy</li>
    <li class="service-item"><svg width="20" height="16" viewBox="0 0 20 16"><ellipse cx="10" cy="8" rx="9" ry="7" fill="var(--teal)"/><circle cx="10" cy="8" r="3" fill="#fff"/></svg>Support Coordination Levels 1 &amp; 2</li>
    <li class="service-item"><svg width="20" height="16" viewBox="0 0 20 16"><ellipse cx="10" cy="8" rx="9" ry="7" fill="var(--teal)"/><circle cx="10" cy="8" r="3" fill="#fff"/></svg>Short Term Accommodation - STA Respite</li>
    <li class="service-item"><svg width="20" height="16" viewBox="0 0 20 16"><ellipse cx="10" cy="8" rx="9" ry="7" fill="var(--teal)"/><circle cx="10" cy="8" r="3" fill="#fff"/></svg>Drop In Supports</li>
    <li class="service-item"><svg width="20" height="16" viewBox="0 0 20 16"><ellipse cx="10" cy="8" rx="9" ry="7" fill="var(--teal)"/><circle cx="10" cy="8" r="3" fill="#fff"/></svg>Community Access</li>
  </ul>

  <div class="grass-wash" role="img" aria-label="Watercolour grass band in teal, pink and orange"></div>
</main>
</body>
</html>
```